Photo booth placards - Customers select after a game for a fun group photo

i am wanting 24 photobooth placards to fit on a peice of corflute (2400 x 1220) all on one file to print. Must be Bright and fun, each one different style /colour.
Escape room placards- approx. A3(file size with all on the one file 2400 x 1220) Require as a source file and high res pdf.
1. Photo Booth - Grab a prop and strike a post (this one is for the box that will contain the other signs)
2. Photo Booth - Grab a prop and strike a post (this one is for the box that will contain the other signs)
3. GENIUS
4. Nailed it!
5. I’m Awesome
6. We escaped
7. (arrow left) They were no help (Arrow Right)
8. We did it!
9. I’m still confused??
10. They Should have listened to me
11. Weakest link (arrow)
12. I’m the smart one
13. Escape Artist
14. I did EVERYTHING
15. Winners
16. No one listens to me
17. I survived by my wits (and good looks)
18. Escaped in time - woohoo!
19. We ALMOST beat the clock
20. (arrow left) Genius – We Escaped- Sidekick (arrow right)
21. We suck
22. I’m glad they’re smart
23. Mission completed
24. I’m with stupid (arrow)

some sample ideas attached...

```html
<!DOCTYPE html>
<html lang="en">
<head>
<meta charset="utf-8">
<title>Escape Room Photo Booth Placards</title>
<link href="https://fonts.googleapis.com/css2?family=Anton&family=Bree+Serif&family=Fredoka:wght@500;600;700&family=Luckiest+Guy&family=Titan+One&family=Boogaloo&family=Montserrat:wght@500;600;700&family=Kalam:wght@700&family=Lilita+One&family=Oswald:wght@600;700&family=Rowdies:wght@700&family=Patrick+Hand&display=swap" rel="stylesheet">
<style>
:root{
  --black:#0c0c0c;
  --white:#ffffff;
  --flame-red:#b51a1a;
  --parchment-light:#e9c98c;
  --parchment-dark:#b5833c;
  --wood-light:#d69a55;
  --wood-dark:#9c5e26;
  --wood-text:#5a2e0e;
  --sun-yellow:#ffd400;
  --pop-red:#e0241c;
  --escape-green:#1e6b2c;
  --lemon:#f7f56f;
  --help-blue:#1aa7e8;
  --navy:#343b57;
  --trophy-gold:#f2b42a;
  --plum:#2e0f2a;
  --violet:#8c2bb8;
  --magenta-paint:#c43ab8;
  --gold:#c9a23a;
  --hot-pink:#e0206b;
  --splash-orange:#f26a10;
  --coal:#2a2a2a;
  --crimson:#ad0f4b;
  --night:#0d1430;
  --alarm-red:#c8102e;
  --sky:#5ab7ef;
  --suck-pink:#e61fa0;
  --chalk-teal:#137a6e;
  --mission-orange:#f5a21a;
  --dusk:#2a2222;
  --tan:#c9a36a;
  --comic:'Luckiest Guy','Titan One',sans-serif;
}
*{box-sizing:border-box;margin:0;padding:0}
html,body{width:1200px;height:610px;overflow:hidden;background:var(--white)}
.placard-sheet{
  width:1200px;height:610px;
  display:grid;
  grid-template-columns:repeat(6,200px);
  grid-template-rows:repeat(4,152.5px);
}
.placard{position:relative;overflow:hidden}
.placard > *{position:absolute}
.placard p,.placard h1{white-space:nowrap}
.art{display:block}
.center-x{left:0;right:0;text-align:center}

/* 1 */
.booth-flame{background:var(--black)}
.booth-flame .title{top:8px;font-family:'Anton',sans-serif;font-size:30px;color:#d2281e;letter-spacing:.5px}
.booth-flame .flames{left:0;top:50px;width:200px;height:45px;background:linear-gradient(#0c0c0c,var(--flame-red))}
.booth-flame .band{left:0;top:92px;width:200px;height:61px;background:var(--flame-red)}
.booth-flame .tagline{top:88px;font-family:'Fredoka',sans-serif;font-weight:600;font-size:22px;line-height:26px;color:var(--white)}

/* 2 */
.booth-classic{background:var(--white)}
.booth-classic .mascot{left:62px;top:3px;width:76px;height:44px;background:#d8d8d8;border-radius:4px}
.booth-classic .rule{left:58px;top:48px;width:96px;height:1px;background:var(--black)}
.booth-classic .title{top:50px;font-family:'Bree Serif',serif;font-size:24px;color:var(--black)}
.booth-classic .band{left:0;top:81px;width:200px;height:72px;background:var(--black)}
.booth-classic .tagline{top:88px;font-family:'Fredoka',sans-serif;font-weight:500;font-size:22px;line-height:26px;color:var(--white)}

/* parchment */
.parchment{background:radial-gradient(circle at 50% 45%,var(--parchment-light),var(--parchment-dark))}

/* 3 */
.genius .bulb{left:82px;top:18px;width:36px;height:54px;background:var(--sun-yellow);border-radius:18px 18px 6px 6px}
.genius .word{top:70px;font-family:'Titan One',sans-serif;font-size:44px;color:var(--black);-webkit-text-stroke:1px var(--sun-yellow);letter-spacing:1px}

/* 4 */
.nailed{background:linear-gradient(100deg,var(--wood-light),var(--wood-dark))}
.nailed .word{left:20px;top:14px;font-family:'Anton',sans-serif;font-size:38px;line-height:44px;color:var(--wood-text)}
.nailed .hammer{left:132px;top:38px;width:68px;height:52px;background:#b0622a;border-radius:6px}

/* 5 */
.awesome{background:#fff4ec}
.awesome .burst{left:20px;top:18px;width:160px;height:118px;background:radial-gradient(ellipse,var(--sun-yellow) 45%,#f58a1e 70%,var(--pop-red) 90%);border-radius:50%}
.awesome .word{top:48px;font-family:var(--comic);font-size:24px;line-height:26px;color:var(--black)}

/* 6 */
.escaped .key{left:18px;top:22px;width:44px;height:48px;background:#e8dc3a;border-radius:6px}
.escaped .lock{left:150px;top:16px;width:38px;height:52px;background:#f0b820;border-radius:6px}
.escaped .word{top:32px;font-family:var(--comic);font-size:36px;line-height:42px;color:var(--escape-green)}

/* 7 */
.no-help{background:var(--lemon)}
.no-help .arrow-top{left:60px;top:14px}
.no-help .arrow-bottom{left:56px;top:110px}
.no-help .word{top:52px;font-family:var(--comic);font-size:25px;line-height:28px;color:var(--help-blue);-webkit-text-stroke:1.2px var(--black);letter-spacing:1px}

/* 8 */
.did-it{background:var(--navy)}
.did-it .trophy{left:72px;top:16px;width:56px;height:70px;background:var(--trophy-gold);border-radius:8px 8px 14px 14px}
.did-it .word{top:88px;font-family:'Fredoka',sans-serif;font-weight:700;font-size:34px;color:var(--white)}

/* 9 */
.confused{background:var(--white)}
.confused .ground{left:0;top:0}
.confused .line1{left:12px;top:10px;font-family:'Anton',sans-serif;font-size:34px;color:var(--black)}
.confused .line2{left:12px;top:54px;font-family:'Anton',sans-serif;font-size:20px;color:var(--black)}
.confused .panda{left:128px;top:40px;width:62px;height:80px;background:#6a6a6a;border-radius:30px}

/* 10 */
.listened{background:radial-gradient(ellipse at 40% 50%,var(--magenta-paint),var(--violet) 55%,#5a1a8a)}
.listened .word{top:24px;font-family:'Boogaloo',sans-serif;font-size:30px;line-height:37px;color:var(--white)}

/* 11 */
.weakest{background:var(--plum)}
.weakest .word{right:22px;top:14px;text-align:right;font-family:'Oswald',sans-serif;font-weight:700;font-size:40px;line-height:42px;color:var(--white)}
.weakest .arrow{left:17px;top:108px}

/* 12 */
.smart-one{background:var(--black)}
.smart-one .corner{width:36px;height:30px;background:var(--gold);opacity:.55}
.smart-one .c-tl{left:6px;top:6px}.smart-one .c-tr{right:6px;top:6px}
.smart-one .c-bl{left:6px;bottom:6px}.smart-one .c-br{right:6px;bottom:6px}
.smart-one .line1{top:34px;font-family:'Montserrat',sans-serif;font-weight:500;font-size:40px;color:var(--white)}
.smart-one .line2{top:82px;font-family:'Montserrat',sans-serif;font-weight:500;font-size:27px;color:var(--white)}

/* 13 */
.artist{background:var(--white)}
.artist .puzzle{left:82px;top:0;width:118px;height:153px;background:linear-gradient(135deg,#e63a8a,#3aa0e6 50%,#f5c21a)}
.artist .word{left:16px;top:52px;font-family:'Bree Serif',serif;font-size:34px;line-height:44px;color:var(--hot-pink);text-align:center}

/* 14 */
.everything{background:var(--black)}
.everything .splash{left:0;top:0;width:200px;height:83px;background:radial-gradient(circle at 20% 30%,#5a2a0c,#0c0c0c 70%)}
.everything .line1{top:10px;font-family:'Lilita One',sans-serif;font-size:56px;line-height:66px;color:var(--white);letter-spacing:3px}
.everything .band{left:0;top:83px;width:200px;height:70px;background:var(--splash-orange)}
.everything .line2{top:90px;font-family:'Anton',sans-serif;font-size:36px;color:var(--white)}

/* 15 */
.winners{background:radial-gradient(circle,#3a3a3a,#1a1a1a)}
.winners .laurel{left:20px;top:10px;width:160px;height:132px;border-radius:50%;border:14px solid var(--sun-yellow);opacity:.85}
.winners .word{top:58px;font-family:'Boogaloo',sans-serif;font-size:30px;color:var(--sun-yellow)}

/* 16 */
.no-one{background:var(--crimson)}
.no-one .line1{top:18px;font-family:'Montserrat',sans-serif;font-weight:500;font-size:25px;color:var(--white)}
.no-one .line2{top:42px;font-family:'Montserrat',sans-serif;font-weight:600;font-size:48px;color:var(--white)}
.no-one .line3{top:104px;font-family:'Montserrat',sans-serif;font-weight:500;font-size:27px;color:var(--white)}

/* 17 */
.wits{background:linear-gradient(var(--night),#1a2240)}
.wits .trees{left:0;top:118px;width:200px;height:35px;background:linear-gradient(transparent,#05070f 40%)}
.wits .word{top:18px;font-family:'Kalam',cursive;font-size:25px;line-height:31px;color:var(--white)}
.wits .word small{font-size:20px;display:block}

/* 18 */
.in-time{background:var(--alarm-red)}
.in-time .rocket{left:138px;top:8px;width:52px;height:86px;background:#9aa5ad;border-radius:26px 26px 8px 8px}
.in-time .word{left:12px;top:20px;font-family:'Montserrat',sans-serif;font-weight:600;font-size:25px;line-height:33px;color:var(--white)}
.in-time .woohoo{left:10px;top:92px;font-family:'Montserrat',sans-serif;font-weight:700;font-size:37px;color:var(--white)}

/* 19 */
.clock{background:var(--sky)}
.clock .word{right:14px;top:14px;text-align:right;font-family:'Montserrat',sans-serif;font-weight:700;font-size:25px;line-height:31px;color:var(--black)}
.clock .character{left:6px;top:64px;width:92px;height:84px;background:#eaf4fb;border-radius:40px}
.clock .floor{left:0;top:146px;width:200px;height:7px;background:#3f8fc2}

/* 20 */
.sidekick .genius{right:14px;top:12px;font-family:'Boogaloo',sans-serif;font-size:32px;color:var(--black)}
.sidekick .middle{top:58px;font-family:'Patrick Hand',sans-serif;font-size:23px;color:var(--black)}
.sidekick .side{left:20px;top:96px;font-family:'Boogaloo',sans-serif;font-size:38px;color:var(--black)}
.sidekick .arrow-left{left:14px;top:18px}
.sidekick .arrow-right{left:150px;top:112px}
.sidekick .key{left:12px;top:60px;width:22px;height:26px;background:#c8c8c8;border-radius:5px}
.sidekick .lock{left:172px;top:56px;width:24px;height:30px;background:#d8b020;border-radius:5px}

/* 21 */
.we-suck{background:var(--black)}
.we-suck .word{top:38px;font-family:'Anton',sans-serif;font-size:56px;line-height:1;color:var(--suck-pink)}
.we-suck .word .we{color:var(--black);-webkit-text-stroke:2px var(--suck-pink);margin-right:10px}
.we-suck .word .suck{display:inline-block;transform:skewX(-10deg)}

/* 22 */
.glad{background:radial-gradient(circle at 40% 40%,#1f8c7e,var(--chalk-teal) 60%,#0d5a52)}
.glad .word{top:20px;font-family:'Rowdies',sans-serif;font-weight:700;font-size:30px;line-height:38px;color:var(--white)}

/* 23 */
.mission{background:#1f1f1f}
.mission .line1{top:36px;font-family:'Rowdies',sans-serif;font-weight:700;font-size:32px;color:var(--mission-orange)}
.mission .line2{top:72px;font-family:'Rowdies',sans-serif;font-weight:700;font-size:31px;color:var(--white)}

/* 24 */
.stupid{background:var(--dusk)}
.stupid .line1{top:14px;left:40px;right:0;text-align:center;font-family:'Montserrat',sans-serif;font-weight:600;font-size:27px;color:var(--white)}
.stupid .line2{top:40px;left:30px;right:0;text-align:center;font-family:'Kalam',cursive;font-size:40px;color:var(--tan)}
.stupid .arrow{left:52px;top:100px}
</style>
</head>
<body>
<main class="placard-sheet">

  <section class="placard booth-flame">
    <h1 class="title center-x">PHOTO BOOTH</h1>
    <div class="flames" role="img" aria-label="Red flames rising into the black header"></div>
    <div class="band"></div>
    <p class="tagline center-x">Grab a prop and<br>strike a post</p>
  </section>

  <section class="placard booth-classic">
    <div class="mascot" role="img" aria-label="Line drawing of a cat holding a camera"></div>
    <div class="rule"></div>
    <h1 class="title center-x">Photo Booth</h1>
    <div class="band"></div>
    <p class="tagline center-x">Grab a prop and<br>strike a post</p>
  </section>

  <section class="placard parchment genius">
    <div class="bulb" role="img" aria-label="Glowing yellow light bulb"></div>
    <p class="word center-x">GENIUS</p>
  </section>

  <section class="placard nailed">
    <p class="word">Nailed<br>it!</p>
    <div class="hammer" role="img" aria-label="Hammer with red handle and scattered nails"></div>
  </section>

  <section class="placard awesome">
    <div class="burst" role="img" aria-label="Red and yellow comic starburst on a field of little stars"></div>
    <p class="word center-x">I’m<br>Awesome</p>
  </section>

  <section class="placard parchment escaped">
    <div class="key" role="img" aria-label="Yellow key"></div>
    <div class="lock" role="img" aria-label="Open golden padlock"></div>
    <p class="word center-x">We<br>escaped</p>
  </section>

  <section class="placard no-help">
    <svg class="arrow-top art" width="80" height="34" viewBox="0 0 80 34"><path d="M2 10H52V2L78 17 52 32V24H2Z" fill="#7ed321" stroke="#0c0c0c" stroke-width="2"/></svg>
    <p class="word center-x">THEY WERE<br>NO HELP</p>
    <svg class="arrow-bottom art" width="80" height="34" viewBox="0 0 80 34"><path d="M78 10H28V2L2 17 28 32V24H78Z" fill="#f5962a" stroke="#0c0c0c" stroke-width="2"/></svg>
  </section>

  <section class="placard did-it">
    <div class="trophy" role="img" aria-label="Gold trophy cup with a winner ribbon"></div>
    <p class="word center-x">We did it!</p>
  </section>

  <section class="placard confused">
    <svg class="ground art" width="200" height="153" viewBox="0 0 200 153"><path d="M0 108Q100 88 200 116V153H0Z" fill="#0c0c0c"/></svg>
    <p class="line1">I’m still</p>
    <p class="line2">confused??</p>
    <div class="panda" role="img" aria-label="Puzzled panda with question marks overhead"></div>
  </section>

  <section class="placard listened">
    <p class="word center-x">They Should<br>have listened<br>to me</p>
  </section>

  <section class="placard weakest">
    <p class="word">Weakest<br>link</p>
    <svg class="arrow art" width="166" height="30" viewBox="0 0 166 30"><path d="M0 15L26 1V10H166V20H26V29Z" fill="#ffffff"/></svg>
  </section>

  <section class="placard smart-one">
    <div class="corner c-tl" role="img" aria-label="Gold ornamental corner"></div>
    <div class="corner c-tr" role="img" aria-label="Gold ornamental corner"></div>
    <div class="corner c-bl" role="img" aria-label="Gold ornamental corner"></div>
    <div class="corner c-br" role="img" aria-label="Gold ornamental corner"></div>
    <p class="line1 center-x">I’m the</p>
    <p class="line2 center-x">smart one</p>
  </section>

  <section class="placard artist">
    <div class="puzzle" role="img" aria-label="Colourful jigsaw pieces scattered down the right edge"></div>
    <p class="word">Escape<br>Artist</p>
  </section>

  <section class="placard everything">
    <div class="splash" role="img" aria-label="Orange paint splatter on black"></div>
    <p class="line1 center-x">I did</p>
    <div class="band"></div>
    <p class="line2 center-x">EVERYTHING</p>
  </section>

  <section class="placard winners">
    <div class="laurel" role="img" aria-label="Golden laurel wreath"></div>
    <p class="word center-x">Winners</p>
  </section>

  <section class="placard no-one">
    <p class="line1 center-x">No one</p>
    <p class="line2 center-x">listens</p>
    <p class="line3 center-x">to me</p>
  </section>

  <section class="placard wits">
    <div class="trees" role="img" aria-label="Starry night sky over a forest silhouette"></div>
    <p class="word center-x">I survived by<br>my wits<small>(and good looks)</small></p>
  </section>

  <section class="placard in-time">
    <div class="rocket" role="img" aria-label="Silver rocket with green fins"></div>
    <p class="word">Escaped<br>in time -</p>
    <p class="woohoo">woohoo!</p>
  </section>

  <section class="placard clock">
    <p class="word">We ALMOST<br>beat the<br>clock</p>
    <div class="character" role="img" aria-label="Running alarm clock character"></div>
    <div class="floor"></div>
  </section>

  <section class="placard parchment sidekick">
    <svg class="arrow-left art" width="76" height="26" viewBox="0 0 76 26"><path d="M0 13L22 0V26Z" fill="#0c0c0c"/><g stroke="#0c0c0c" stroke-width="2"><line x1="14" y1="3" x2="76" y2="3"/><line x1="14" y1="8" x2="76" y2="8"/><line x1="14" y1="13" x2="76" y2="13"/><line x1="14" y1="18" x2="76" y2="18"/><line x1="14" y1="23" x2="76" y2="23"/></g></svg>
    <p class="genius">Genius</p>
    <div class="key" role="img" aria-label="Silver key"></div>
    <p class="middle center-x">We Escaped</p>
    <div class="lock" role="img" aria-label="Open striped padlock"></div>
    <p class="side">Sidekick</p>
    <svg class="arrow-right art" width="42" height="24" viewBox="0 0 42 24"><path d="M0 8H26V0L42 12 26 24V16H0Z" fill="#0c0c0c"/></svg>
  </section>

  <section class="placard we-suck">
    <p class="word center-x"><span class="we">We</span><span class="suck">suck</span></p>
  </section>

  <section class="placard glad">
    <p class="word center-x">I’m glad<br>they’re<br>smart</p>
  </section>

  <section class="placard mission">
    <p class="line1 center-x">Mission</p>
    <p class="line2 center-x">completed</p>
  </section>

  <section class="placard stupid">
    <p class="line1">I’m with</p>
    <p class="line2">stupid</p>
    <svg class="arrow art" width="104" height="42" viewBox="0 0 104 42"><path d="M2 21L34 2V12H102V30H34V40Z" fill="none" stroke="#ffffff" stroke-width="3" stroke-linejoin="round"/><g stroke="#ffffff" stroke-width="2"><line x1="44" y1="12" x2="44" y2="30"/><line x1="54" y1="12" x2="54" y2="30"/><line x1="64" y1="12" x2="64" y2="30"/><line x1="74" y1="12" x2="74" y2="30"/><line x1="84" y1="12" x2="84" y2="30"/><line x1="94" y1="12" x2="94" y2="30"/></g></svg>
  </section>

</main>
</body>
</html>
```